Business Card Design Project

We are a construction company in Orange County, CA. We need a two sided business card. We would like the back to be our logo with web URL. Front should included Name, title, address, phone, fax and email address.

our address is
627 West Dorrance Blvd, Suite 308
Anaheim, CA 92718

Our logo files are attached.

Construction

```html
<!DOCTYPE html>
<html lang="en">
<head>
<meta charset="utf-8">
<title>Kestron Business Card</title>
<link href="https://fonts.googleapis.com/css2?family=Open+Sans:wght@400;600;700;800&display=swap" rel="stylesheet">
<style>
  :root {
    --brand-blue: #1a4a7e;
    --paper: #ffffff;
    --ink-grey: #555555;
    --rule-grey: #6a6a6a;
    --swoosh-grey: #5c5c5c;
    --backdrop: #e6e6e6;
  }
  html, body {
    margin: 0;
    padding: 0;
    width: 1200px;
    height: 402px;
    overflow: hidden;
    background: var(--backdrop);
    font-family: "Open Sans", Arial, sans-serif;
  }
  .stage {
    position: relative;
    width: 1231px;
    height: 412px;
    transform: scale(0.9748);
    transform-origin: 0 0;
  }
  .card {
    position: absolute;
    top: 44px;
    width: 525px;
    height: 299px;
    border-radius: 26px;
    overflow: hidden;
  }
  .card--front { left: 67px; background: var(--paper); }
  .card--back { left: 646px; background: var(--brand-blue); }

  .wordmark {
    position: absolute;
    left: 0;
    width: 100%;
    text-align: center;
    font-weight: 800;
    line-height: 1;
    letter-spacing: -1px;
    margin: 0;
  }
  .tagline {
    position: absolute;
    left: 0;
    width: 100%;
    text-align: center;
    font-weight: 600;
    margin: 0;
    white-space: nowrap;
  }
  .card--front .wordmark { top: 30px; font-size: 66px; color: var(--brand-blue); }
  .card--front .tagline { top: 98px; font-size: 11px; letter-spacing: 4.6px; color: var(--brand-blue); }
  .card--back .wordmark { top: 100px; font-size: 78px; color: var(--paper); }
  .card--back .tagline { top: 180px; font-size: 13px; letter-spacing: 5.6px; color: var(--paper); }

  .address {
    position: absolute;
    right: 277px;
    top: 147px;
    margin: 0;
    font-style: normal;
    font-size: 13px;
    line-height: 17px;
    color: var(--ink-grey);
    text-align: right;
    white-space: nowrap;
  }
  .divider {
    position: absolute;
    left: 262px;
    top: 138px;
    width: 1px;
    height: 74px;
    background: var(--rule-grey);
  }
  .contacts {
    position: absolute;
    left: 277px;
    top: 140px;
    margin: 0;
    padding: 0;
    list-style: none;
    font-size: 13px;
    line-height: 17px;
    color: var(--ink-grey);
  }
  .contacts li { display: flex; align-items: center; gap: 6px; white-space: nowrap; }
  .contacts svg { width: 11px; height: 11px; fill: var(--ink-grey); flex: none; }

  .wave { position: absolute; left: 0; top: 0; width: 525px; height: 299px; }
  .holder {
    position: absolute;
    left: 51px;
    top: 259px;
    margin: 0;
    font-size: 16px;
    font-weight: 700;
    color: var(--paper);
  }
</style>
</head>
<body>
<div class="stage">
  <section class="card card--front" aria-label="Card front">
    <p class="wordmark">KESTRON</p>
    <p class="tagline">BUILD • RENOVATE • MANAGE</p>

    <address class="address">627 West Dorrance Blvd<br>Suite 308, Anaheim<br>CA 92718</address>
    <div class="divider"></div>
    <ul class="contacts">
      <li><svg viewBox="0 0 12 12"><path d="M3 1l2 2.5-1.2 1.3c.7 1.4 1.7 2.4 3.1 3.1L8.2 6.7 10.7 8.7 9.6 10.8C5.2 10.6 1.4 6.8 1.2 2.4z"/></svg>01-555-0142</li>
      <li><svg viewBox="0 0 12 12"><rect x="3" y="1" width="6" height="3"/><rect x="1" y="4.5" width="10" height="4.5" rx="1"/><rect x="3" y="8" width="6" height="3"/></svg>01-555-0187</li>
      <li><svg viewBox="0 0 12 12"><path d="M1 2.5h10v1L6 6.8 1 3.5z"/><path d="M1 5l5 3.3L11 5v4.5H1z"/></svg>info@kestron.co</li>
      <li><svg viewBox="0 0 12 12"><circle cx="6" cy="6" r="5"/><path d="M1 6h10M6 1v10" stroke="#fff" stroke-width=".8" fill="none"/></svg>www.kestron.co</li>
    </ul>

    <svg class="wave" viewBox="0 0 525 299" aria-hidden="true">
      <path d="M0 247 C120 240 260 262 400 280 C460 287 500 275 525 258 L525 299 L0 299 Z" fill="var(--brand-blue)"/>
      <path d="M32 238 C140 228 300 248 470 276 C320 252 160 236 32 241 Z" fill="var(--swoosh-grey)"/>
    </svg>
    <p class="holder">Your Name, Title</p>
  </section>

  <section class="card card--back" aria-label="Card back">
    <p class="wordmark">KESTRON</p>
    <p class="tagline">BUILD • RENOVATE • MANAGE</p>
  </section>
</div>
</body>
</html>
```